Create a memorable Web Design for real estate branding

we are a Minnepolis brokerage and boutique housing specialist with over 27 years of experience in the Global furnished housing industry, servicing the Greater Los Angeles area. Specializing in “warm environments” we offer a customized approach to satisfying our guests and client’s needs by offering a wide array of options in highly desirable areas. Additionally, Lantern Dwelling Partners offers assistance and expertise to home buyers, sellers and investors.

Industry/Entity Type

Real Estate

Number of Pages Required

1 page

Font styles to use
Serif
Sans Serif
Decorative

```html
<!DOCTYPE html>
<html lang="en">
<head>
<meta charset="utf-8">
<title>Lantern Dwelling Real Estate</title>
<link rel="stylesheet" href="https://fonts.googleapis.com/css2?family=Cinzel:wght@600;700&family=Marcellus&family=Raleway:wght@400;500;600;700&display=swap">
<style>
:root{
  --teal:#0fa88f;
  --teal-deep:#0a7f6d;
  --teal-dark:#0d5d52;
  --lime:#9cc63b;
  --ink:#333a3a;
  --muted:#6b6f70;
  --light:#f1f1f1;
  --white:#ffffff;
}
*{margin:0;padding:0;box-sizing:border-box}
html,body{width:1200px;height:2699px;overflow:hidden}
body{position:relative;background:var(--white);font-family:"Raleway",Arial,sans-serif;color:var(--ink)}
.abs{position:absolute}

/* header */
.site-header{position:absolute;left:0;top:0;width:1200px;height:139px;background:var(--white);border-top:4px solid var(--teal)}
.brand{position:absolute;left:99px;top:30px;color:var(--teal);font-family:"Raleway",sans-serif;font-weight:700;line-height:1}
.brand .name{font-size:40px;letter-spacing:.5px}
.brand .tag{font-size:24px;margin-top:8px;margin-left:118px;letter-spacing:1px}
.social{position:absolute;display:flex;gap:14px}
.social span{display:block;width:40px;height:40px;border:2px solid #333;border-radius:50%}
.quick{position:absolute;left:940px;top:25px;display:flex;align-items:center;gap:16px}
.quick .ring{width:42px;height:42px;border-radius:50%;background:var(--teal);display:flex;align-items:center;justify-content:center;box-shadow:0 0 0 3px #c7ece5}
.quick p{font-size:14px;line-height:22px;color:#222}
.main-nav{position:absolute;top:100px;left:0;width:1200px;font-size:15px;font-weight:500;color:#222}
.main-nav a{position:absolute;color:inherit;text-decoration:none}
.main-nav a.active{color:var(--teal)}

/* hero */
.hero{position:absolute;left:0;top:139px;width:1200px;height:554px;background:linear-gradient(180deg,#1a1b3f 0%,#3b2f63 40%,#285066 70%,#1d3a3c 100%)}
.hero h1{position:absolute;left:0;width:1200px;text-align:center;font-family:"Cinzel",serif;font-weight:700;color:var(--white);font-size:44px;letter-spacing:2px;line-height:72px;top:117px}
.hero-arrows{position:absolute;top:303px;left:553px;display:flex;gap:18px}
.hero-arrows span{width:36px;height:36px;border:2px solid rgba(255,255,255,.8);border-radius:50%;display:flex;align-items:center;justify-content:center}

/* service cards */
.services{position:absolute;left:99px;top:534px;width:1002px;height:414px;display:flex}
.card{width:334px;height:414px;padding:18px 17px 0;color:var(--white);position:relative}
.card.teal{background:var(--teal)}
.card.lime{background:var(--lime)}
.card h2{font-family:"Marcellus",serif;font-weight:400;font-size:30px;line-height:1.1}
.card p{font-size:12.5px;line-height:21px;margin-top:12px;height:64px}
.card .photo{width:300px;height:244px;margin-top:15px}
.services-shadow{position:absolute;left:99px;top:940px;width:1002px;height:30px}

/* about */
.section-title{position:absolute;left:0;width:1200px;text-align:center;font-family:"Cinzel",serif;font-weight:700;font-size:36px;color:var(--teal);letter-spacing:1px}
.lead{position:absolute;left:150px;width:900px;text-align:center;font-size:12.5px;line-height:23px;color:var(--muted)}
.facts{position:absolute;left:99px;top:1180px;width:1002px;height:140px}
.fact{position:absolute;width:200px;text-align:center;top:0}
.fact svg{display:block;margin:0 auto}
.fact .label{font-size:15px;font-weight:500;margin-top:14px;color:#222}
.fact .value{font-size:20px;font-weight:600;margin-top:8px;color:#222}
.fact-divider{position:absolute;top:30px;width:1px;height:90px;background:#cfcfcf}
.rule{position:absolute;left:99px;top:1361px;width:1002px;height:2px;background:var(--teal)}

/* gallery */
.gallery{position:absolute;left:0;top:1526px;width:1200px;height:444px;display:grid;grid-template-columns:repeat(4,300px);grid-template-rows:repeat(2,222px)}
.tile{position:relative}
.tile .overlay{position:absolute;inset:0;background:rgba(20,20,20,.55);display:flex;flex-direction:column;align-items:center;justify-content:center;color:var(--white)}
.tile .overlay h3{font-size:20px;font-weight:500}
.tile .overlay .tools{display:flex;gap:12px;margin-top:18px}
.tile .overlay .tools span{width:28px;height:28px;border:2px solid var(--white);display:flex;align-items:center;justify-content:center}

/* promo band */
.promo{position:absolute;left:0;top:1970px;width:1200px;height:128px;background:var(--lime);color:var(--white)}
.promo .brand{color:var(--white);left:99px;top:30px}
.promo .divider{position:absolute;left:408px;top:24px;width:2px;height:82px;background:var(--white)}
.promo p{position:absolute;left:432px;top:30px;width:420px;font-size:12.5px;line-height:23px;font-weight:500;text-align:justify}
.promo .cta{position:absolute;left:930px;top:47px;width:136px;height:42px;border:2px solid var(--white);font-size:13px;font-weight:500;display:flex;align-items:center;justify-content:center}

/* partners */
.partners{position:absolute;left:0;top:2098px;width:1200px;height:162px;background:var(--light)}
.partners .nav-btn{position:absolute;top:69px;width:40px;height:40px;border:2px solid #222;border-radius:50%;display:flex;align-items:center;justify-content:center}
.partner-badge{position:absolute;top:66px;height:36px;width:120px;background:#c4c6c6;border-radius:4px}

/* contact */
.contact{position:absolute;left:0;top:2260px;width:1200px;height:385px;background:linear-gradient(180deg,#10695c 0%,#0c574d 100%);color:var(--white)}
.contact h2{position:absolute;left:99px;top:50px;font-size:29px;font-weight:500}
.contact .underline{position:absolute;left:99px;top:90px;width:133px;height:3px;background:var(--white)}
.info{position:absolute;left:99px;display:flex;align-items:center;gap:22px;font-size:15px;font-weight:600;line-height:24px}
.info .ic{width:48px;height:48px;border-radius:50%;border:2px solid var(--white);display:flex;align-items:center;justify-content:center;flex:none}
.info .ic.filled{background:var(--teal);border-color:var(--teal)}
.form-title{position:absolute;left:484px;top:50px;font-size:18px;font-weight:600}
.field{position:absolute;background:rgba(255,255,255,.8);color:#667;font-size:13px;padding:10px 12px;height:40px}
.send{position:absolute;left:484px;top:315px;width:117px;height:36px;background:var(--teal);font-size:14px;font-weight:500;display:flex;align-items:center;justify-content:center}

/* footer */
.site-footer{position:absolute;left:0;top:2645px;width:1200px;height:54px;background:linear-gradient(180deg,#13b99c,#0ea084);color:var(--white)}
.site-footer p{position:absolute;left:99px;top:18px;font-size:13.5px;font-weight:500}
.site-footer .social{left:980px;top:10px;gap:10px}
.site-footer .social span{width:34px;height:34px;border-color:var(--white)}
</style>
</head>
<body>

<header class="site-header">
  <div class="brand"><div class="name">Lantern Dwelling</div><div class="tag">Real Estate</div></div>
  <div class="social" style="left:703px;top:22px"><span></span><span></span><span></span><span></span></div>
  <div class="quick">
    <div class="ring"><svg width="20" height="20" viewBox="0 0 24 24"><path d="M6.6 10.8a15 15 0 0 0 6.6 6.6l2.2-2.2a1 1 0 0 1 1-.25 11.4 11.4 0 0 0 3.6.57 1 1 0 0 1 1 1V20a1 1 0 0 1-1 1A17 17 0 0 1 3 4a1 1 0 0 1 1-1h3.5a1 1 0 0 1 1 1c0 1.25.2 2.45.57 3.57a1 1 0 0 1-.25 1z" fill="#fff"/></svg></div>
    <p>Quick Contact:<br>1800 4417 2290</p>
  </div>
  <nav class="main-nav">
    <a class="active" style="left:540px">Home</a>
    <a style="left:627px">About Us</a>
    <a style="left:737px">Gallery</a>
    <a style="left:831px">Property</a>
    <a style="left:936px">Video</a>
    <a style="left:1020px">Contact Us</a>
  </nav>
</header>

<section class="hero" role="img" aria-label="Night city skyline with lit towers reflected over water">
  <h1>Specializing<br>“warm environments”</h1>
  <div class="hero-arrows">
    <span><svg width="10" height="12" viewBox="0 0 10 12"><path d="M7 1 2 6l5 5" stroke="#fff" stroke-width="2" fill="none"/></svg></span>
    <span><svg width="10" height="12" viewBox="0 0 10 12"><path d="m3 1 5 5-5 5" stroke="#fff" stroke-width="2" fill="none"/></svg></span>
  </div>
</section>

<svg class="services-shadow" viewBox="0 0 1002 30" preserveAspectRatio="none" aria-hidden="true">
  <path d="M0 0 Q 167 40 334 8 Q 501 40 668 8 Q 835 40 1002 0 L1002 4 Q835 30 668 14 Q501 30 334 14 Q167 30 0 4Z" fill="#d7d7d7"/>
</svg>
<section class="services">
  <article class="card teal">
    <h2>Residential</h2>
    <p>Nemo enim ipsam voluptatem quia voluptas sit aspernatur autenre odit auton fugitin sed quia consequuntur magni dolores</p>
    <div class="photo" role="img" aria-label="Apartment towers beyond a green lawn" style="background:linear-gradient(180deg,#b9d6ee 0%,#e7eef2 45%,#6f9a4e 70%,#4e7a33 100%)"></div>
  </article>
  <article class="card lime">
    <h2>Commercial</h2>
    <p>Nemo enim ipsam voluptatem quia voluptas sit aspernatur autenre odit auton fugitin sed quia consequuntur magni dolores</p>
    <div class="photo" role="img" aria-label="Glass office building beside a tree-lined walkway" style="background:linear-gradient(135deg,#7fa9cf 0%,#3f6c8f 45%,#5d8a3f 80%,#9aa49a 100%)"></div>
  </article>
  <article class="card teal">
    <h2>Rental</h2>
    <p>Nemo enim ipsam voluptatem quia voluptas sit aspernatur autenre odit auton fugitin sed quia consequuntur magni dolores</p>
    <div class="photo" role="img" aria-label="Warm furnished dining room with round table" style="background:linear-gradient(180deg,#e6d8c3 0%,#c9a47e 55%,#8c4b2d 100%)"></div>
  </article>
</section>

<h2 class="section-title" style="top:995px">About Property</h2>
<p class="lead" style="top:1060px">Nemo enim ipsam voluptatem quia voluptas sit aspernatur aut odit aut fugit, sed quia consequuntur magni dolores eos qui ratione voluptatem sequi nesciunt. Neque porro quisquam est, qui dolorem ipsum quia dolor sit amet, consectetur, adipisci velit, sed quia non numquam eius modi tempora incidunt ut labore et dolore magnam aliquam quaerat voluptatem. Ut enim ad minima veniam, quis nostrum</p>

<div class="facts">
  <div class="fact" style="left:-35px">
    <svg width="56" height="44" viewBox="0 0 56 44"><g fill="none" stroke="#0fa88f" stroke-width="3"><rect x="6" y="4" width="44" height="16" rx="2"/><rect x="2" y="20" width="52" height="14"/><path d="M6 34v6M50 34v6"/></g><rect x="12" y="10" width="12" height="8" fill="#0fa88f"/><rect x="32" y="10" width="12" height="8" fill="#0fa88f"/></svg>
    <div class="label">BEDROOMS</div><div class="value">3</div></div>
  <div class="fact-divider" style="left:173px"></div>
  <div class="fact" style="left:177px">
    <svg width="48" height="46" viewBox="0 0 48 46"><g fill="none" stroke="#0fa88f" stroke-width="2.5"><rect x="3" y="3" width="32" height="32"/><path d="M13 3v32M24 3v32M3 13h32M3 24h32"/><path d="M44 18v24H20z"/></g></svg>
    <div class="label">SQUARE FEET</div><div class="value">2520</div></div>
  <div class="fact-divider" style="left:389px"></div>
  <div class="fact" style="left:402px">
    <svg width="48" height="46" viewBox="0 0 48 46"><g fill="none" stroke="#0fa88f" stroke-width="3"><path d="M4 22h40v8a10 10 0 0 1-10 10H14A10 10 0 0 1 4 30z"/><path d="M10 22V8a5 5 0 0 1 10 0M12 40l-2 5M36 40l2 5"/></g></svg>
    <div class="label">BATHS</div><div class="value">2</div></div>
  <div class="fact-divider" style="left:610px"></div>
  <div class="fact" style="left:614px">
    <svg width="44" height="46" viewBox="0 0 44 46"><g fill="none" stroke="#0fa88f" stroke-width="3"><rect x="3" y="7" width="38" height="36" rx="2"/><path d="M3 17h38M13 2v9M31 2v9"/></g><g fill="#0fa88f"><rect x="9" y="22" width="6" height="5"/><rect x="19" y="22" width="6" height="5"/><rect x="29" y="22" width="6" height="5"/><rect x="9" y="32" width="6" height="5"/><rect x="19" y="32" width="6" height="5"/><rect x="29" y="32" width="6" height="5"/></g></svg>
    <div class="label">YEAR BUILD</div><div class="value">2016</div></div>
  <div class="fact-divider" style="left:824px"></div>
  <div class="fact" style="left:835px">
    <svg width="48" height="46" viewBox="0 0 48 46"><path d="M24 3 3 16h42z" fill="#0fa88f"/><path d="M12 24h24l5 8v10H7V32z" fill="#0fa88f"/><circle cx="15" cy="35" r="3" fill="#fff"/><circle cx="33" cy="35" r="3" fill="#fff"/><rect x="14" y="26" width="20" height="5" fill="#fff"/></svg>
    <div class="label">CAR PARKING</div><div class="value">1</div></div>
</div>
<div class="rule"></div>

<h2 class="section-title" style="top:1390px">Photo Gallery</h2>
<p class="lead" style="top:1448px;left:200px;width:800px">Real Estate agents are Property consisting of land and the buildings on it, along with its seds naturals resources such seds as crops, minerals, or wate</p>

<section class="gallery">
  <div class="tile" role="img" aria-label="Modern house with terrace at dusk" style="background:linear-gradient(160deg,#c9d2d6,#7d7566 60%,#2e2b26)"></div>
  <div class="tile" role="img" aria-label="Contemporary brick building" style="background:linear-gradient(160deg,#4d4640,#2a2622)">
    <div class="overlay"><h3>Building Specialists</h3>
      <div class="tools">
        <span><svg width="14" height="14" viewBox="0 0 14 14"><circle cx="6" cy="6" r="4" stroke="#fff" stroke-width="2" fill="none"/><path d="m9 9 4 4" stroke="#fff" stroke-width="2"/></svg></span>
        <span><svg width="14" height="14" viewBox="0 0 14 14"><path d="M6 8 8 6M5 5 3 7a2 2 0 0 0 3 3l2-2M9 9l2-2a2 2 0 0 0-3-3L6 6" stroke="#fff" stroke-width="1.6" fill="none"/></svg></span>
      </div></div></div>
  <div class="tile" role="img" aria-label="Brick and glass campus building under blue sky" style="background:linear-gradient(160deg,#3d7fd0,#a8c4e0 45%,#8a4a3a 75%,#5b5148)"></div>
  <div class="tile" role="img" aria-label="White modern building with street trees" style="background:linear-gradient(160deg,#5b9ad8,#cfdfee 50%,#9aa4a0 80%,#6a8a4a)"></div>
  <div class="tile" role="img" aria-label="Glass skyscrapers seen from below" style="background:linear-gradient(160deg,#2a4f8a,#6d8fb8 50%,#c9a85a)"></div>
  <div class="tile" role="img" aria-label="Lit apartment block at twilight" style="background:linear-gradient(180deg,#2d5fa8,#3f7cc0 50%,#6e6a5e 85%,#4a4238)"></div>
  <div class="tile" role="img" aria-label="Hand holding a small model house" style="background:linear-gradient(160deg,#dde3ea,#a9b6c4 50%,#c88a64)"></div>
  <div class="tile" role="img" aria-label="Reflective office towers against sky" style="background:linear-gradient(160deg,#2c5a92,#8fb2d6 50%,#44698f)"></div>
</section>

<section class="promo">
  <div class="brand"><div class="name">Lantern Dwelling</div><div class="tag">Real Estate</div></div>
  <div class="divider"></div>
  <p>Real Estate agents are Property consisting of land and the buildings on it, along with its seds naturals resources such seds as crops, minerals, or water.</p>
  <div class="cta">CONTACT NOW</div>
</section>

<section class="partners">
  <div class="nav-btn" style="left:30px"><svg width="10" height="12" viewBox="0 0 10 12"><path d="M7 1 2 6l5 5" stroke="#222" stroke-width="2" fill="none"/></svg></div>
  <div class="partner-badge" style="left:120px"></div>
  <div class="partner-badge" style="left:290px"></div>
  <div class="partner-badge" style="left:460px"></div>
  <div class="partner-badge" style="left:620px"></div>
  <div class="partner-badge" style="left:780px"></div>
  <div class="partner-badge" style="left:940px"></div>
  <div class="nav-btn" style="left:1130px"><svg width="10" height="12" viewBox="0 0 10 12"><path d="m3 1 5 5-5 5" stroke="#222" stroke-width="2" fill="none"/></svg></div>
</section>

<section class="contact">
  <h2>Contact Us</h2>
  <div class="underline"></div>
  <div class="info" style="top:133px"><div class="ic"><svg width="20" height="16" viewBox="0 0 20 16"><rect x="1" y="1" width="18" height="14" fill="#fff"/><path d="m1 1 9 8 9-8" stroke="#0c574d" stroke-width="2" fill="none"/></svg></div>info@lanterndwelling.com</div>
  <div class="info" style="top:211px"><div class="ic filled"><svg width="16" height="22" viewBox="0 0 16 22"><path d="M8 1a7 7 0 0 0-7 7c0 5 7 13 7 13s7-8 7-13a7 7 0 0 0-7-7z" fill="none" stroke="#fff" stroke-width="2"/><circle cx="8" cy="8" r="2.5" fill="#fff"/></svg></div><span>Lantern Dwelling,<br>48120 Country.</span></div>
  <div class="info" style="top:290px"><div class="ic"><svg width="20" height="20" viewBox="0 0 24 24"><path d="M6.6 10.8a15 15 0 0 0 6.6 6.6l2.2-2.2a1 1 0 0 1 1-.25 11.4 11.4 0 0 0 3.6.57 1 1 0 0 1 1 1V20a1 1 0 0 1-1 1A17 17 0 0 1 3 4a1 1 0 0 1 1-1h3.5a1 1 0 0 1 1 1c0 1.25.2 2.45.57 3.57a1 1 0 0 1-.25 1z" fill="#fff"/></svg></div>1800 4417 2290, 1822 0613 7748</div>

  <div class="form-title">Fill out the form below, and we'll contact you shortly.</div>
  <div class="field" style="left:484px;top:102px;width:290px">First Name</div>
  <div class="field" style="left:810px;top:102px;width:290px">Last Name</div>
  <div class="field" style="left:484px;top:156px;width:290px">Phone Number</div>
  <div class="field" style="left:810px;top:156px;width:290px">E-Mail Address</div>
  <div class="field" style="left:484px;top:210px;width:616px;height:86px">Message</div>
  <div class="send">Send Now</div>
</section>

<footer class="site-footer">
  <p>Copyright © 2016 Lantern Dwelling. All rights reserved</p>
  <div class="social"><span></span><span></span><span></span></div>
</footer>

</body>
</html>
```